A5, portrait
Theme is science
audience is VIPS, politicians, executives
this is a really important event, we want a very classy invitation
include logo for bloom and grow and lantern but lantern one bigger
images attached
Have attached some styles we like but doesn't need to be these colours. If we can incorporate some colours from our logo would be good but don't make too colourful and childish

You’re invited to the official opening and launch of Lantern, Centre of Discovery. an industry first, pioneering, STEM hub.

Saturday 30th April, 2022

10:00 am – 12:00 pm

42 Harlow Lane, Fernwood

Light canapes provided. Dress code is smart/casual

All guests will be given a guided walk through of Australia’s first dedicated STEM education hub for children aged 3-6.

Invitation only

RSVP: 18 April to marketing@bloomandgrow.edu.au

```html
<!DOCTYPE html>
<html lang="en">
<head>
<meta charset="utf-8">
<title>Lantern, Centre of Discovery – Official Opening Invitation</title>
<link href="https://fonts.googleapis.com/css2?family=Tinos:wght@400;700&display=swap" rel="stylesheet">
<style>
  :root {
    --page-bg: #e7e4ec;
    --ink-deep: #0b0916;
    --ink-violet: #2c2650;
    --ink-mid: #231e3f;
    --text-light: #f4f2fa;
    --text-soft: #e6e3f0;
    --rsvp-ink: #2a2640;
    --band-white: #ffffff;
    --brand-blue: #1d9fd9;
    --photo-a: #1c1a55;
    --photo-b: #4d47b8;
    --photo-c: #7a5fd0;
  }
  * { margin: 0; padding: 0; box-sizing: border-box; }
  html, body {
    width: 1200px; height: 900px; overflow: hidden;
    background: var(--page-bg);
  }
  .invitation {
    position: absolute; left: 297px; top: 20px;
    width: 606px; height: 860px;
    overflow: hidden;
    background: linear-gradient(160deg, var(--ink-deep) 0%, var(--ink-mid) 30%, var(--ink-violet) 55%, var(--ink-mid) 78%, var(--ink-deep) 100%);
    font-family: "Tinos", "Times New Roman", serif;
    color: var(--text-light);
    box-shadow: 0 14px 30px rgba(20, 16, 40, 0.28);
  }
  .brand-mark {
    position: absolute; top: 76px; left: 0; width: 100%; height: 44px;
    display: flex; justify-content: center; align-items: center; gap: 12px;
  }
  .brand-mark__dot {
    width: 22px; height: 22px; border-radius: 50%;
    background: var(--text-light);
  }
  .brand-mark__name {
    font-size: 42px; font-weight: 700; letter-spacing: 3px;
    color: var(--text-light); line-height: 1;
  }
  .headline {
    position: absolute; top: 176px; left: 0; width: 100%;
    text-align: center; font-size: 22.5px; line-height: 32px;
    font-weight: 400; color: var(--text-light);
  }
  .event-details {
    position: absolute; top: 295px; left: 156px;
    list-style: none;
  }
  .event-details li {
    display: flex; align-items: center;
    height: 35px; font-size: 21px; color: var(--text-light);
  }
  .event-details svg { width: 17px; height: 17px; margin-right: 18px; fill: var(--text-light); flex: none; }
  .venue-photo {
    position: absolute; top: 417px; left: 0; width: 100%; height: 224px;
    background:
      radial-gradient(ellipse 70px 70px at 50% 52%, rgba(170,160,255,0.55), transparent 100%),
      linear-gradient(90deg, var(--photo-a) 0%, var(--photo-b) 45%, var(--photo-c) 85%, var(--photo-a) 100%);
  }
  .guest-notes {
    position: absolute; top: 655px; left: 0; width: 100%;
    text-align: center; font-size: 15px; line-height: 22px;
    color: var(--text-soft);
  }
  .access-tag {
    position: absolute; top: 760px; left: 224px;
    width: 156px; height: 28px;
    border: 1.5px solid var(--text-light);
    display: flex; align-items: center; justify-content: center;
    font-size: 15px; letter-spacing: 0.3px; color: var(--text-light);
  }
  .partner-mark {
    position: absolute; top: 760px; right: 20px;
    display: flex; align-items: center; gap: 6px;
  }
  .partner-mark__square { width: 14px; height: 14px; background: var(--brand-blue); flex: none; }
  .partner-mark__name { font-size: 15px; font-weight: 700; color: var(--text-light); line-height: 1.1; white-space: nowrap; }
  .rsvp-band {
    position: absolute; left: 0; bottom: 0; width: 100%; height: 41px;
    background: var(--band-white);
    display: flex; align-items: center; justify-content: center;
    font-size: 19px; color: var(--rsvp-ink);
  }
</style>
</head>
<body>
  <main class="invitation">
    <div class="brand-mark">
      <span class="brand-mark__dot"></span>
      <span class="brand-mark__name">LANTERN</span>
    </div>

    <h1 class="headline">You’re invited to the official opening and<br>launch of Lantern, Centre of Discovery.<br>An industry first, pioneering, STEM hub.</h1>

    <ul class="event-details">
      <li>
        <svg viewBox="0 0 24 24" aria-hidden="true"><path d="M5 3h2V1h2v2h6V1h2v2h2a2 2 0 0 1 2 2v16a2 2 0 0 1-2 2H5a2 2 0 0 1-2-2V5a2 2 0 0 1 2-2zm0 6v12h14V9H5zm2 2h3v3H7v-3zm5 0h3v3h-3v-3zm-5 5h3v3H7v-3zm5 0h3v3h-3v-3z"/></svg>
        Saturday 30th April, 2022
      </li>
      <li>
        <svg viewBox="0 0 24 24" aria-hidden="true"><path d="M12 1a11 11 0 1 0 0 22 11 11 0 0 0 0-22zm1 11.4 4.2 2.5-1 1.7L11 13.5V6h2v5.4z"/></svg>
        10:00 am – 12:00 pm
      </li>
      <li>
        <svg viewBox="0 0 24 24" aria-hidden="true"><path d="M12 1a8 8 0 0 0-8 8c0 6 8 14 8 14s8-8 8-14a8 8 0 0 0-8-8zm0 11a3 3 0 1 1 0-6 3 3 0 0 1 0 6z"/></svg>
        42 Harlow Lane, Fernwood
      </li>
    </ul>

    <div class="venue-photo" role="img" aria-label="Photo of a glowing plasma ball on a plinth inside the violet-lit STEM hub"></div>

    <p class="guest-notes">Light canapes provided. Dress code is smart/casual<br>All guests will be given a guided walk through of Australia’s first<br>dedicated STEM education hub for children aged 3-6.</p>

    <div class="access-tag">INVITATION ONLY</div>

    <div class="partner-mark">
      <span class="partner-mark__square"></span>
      <span class="partner-mark__name">Bloom &amp; Grow</span>
    </div>

    <footer class="rsvp-band">RSVP: 18 April to marketing@bloomandgrow.edu.au</footer>
  </main>
</body>
</html>
```